Construction material supplies company business card ****

1. Full company name “K T Masonry Works Ltd”
I am after a Business card design for the company as a whole. We are better known in Solomon Islands as “K T Masonry” for short.

We are a building materials supplier of
Ready Mixed Concrete, Bricks and Blocks,
Quarry products- gravel, aggregates, sand etc.
Cement distributor/retailer of reputable brands.
Other prefab concrete products. Culverts, wave breakers, concrete retaining blocks etc.

2. Competitive Advantage over Competition: Quality, efficient, professional, dependable, reliable

3. We want people to feel trust worthy, high quality, strong when they see our brand

5. No preference to color. Maybe more sturdy and corporate. Not fancy.

Industry/Entity Type

CONSTRUCTION SUPPLY

Contact Information for Business Card

Name, Position, office phone mob phone, email

Requirements
Must have
• the company logo
Nice to have
• would like to see a mixture of designs, of with logo only and also with simple graphic designs to bring out the company whilst still have the strong sturdy professional feeling

```html
<!DOCTYPE html>
<html lang="en">
<head>
<meta charset="utf-8">
<title>K T Masonry – Business Card</title>
<link rel="stylesheet" href="https://fonts.googleapis.com/css2?family=Roboto:wght@400;500;700&display=swap">
<style>
  :root {
    --backdrop: #2a2a2b;
    --navy: #1d3f66;
    --navy-deep: #142f50;
    --navy-band: rgba(10, 32, 60, 0.72);
    --steel: #3a5f88;
    --paper: #e4e4e3;
    --paper-shade: #d3d3d2;
    --ink: #1b3a60;
    --white: #f4f5f7;
  }
  * { box-sizing: border-box; margin: 0; padding: 0; }
  html, body {
    width: 1200px; height: 1138px; overflow: hidden;
    background: var(--backdrop);
    font-family: "Roboto", Arial, sans-serif;
  }
  .canvas { position: relative; width: 1200px; height: 1138px; }

  .card {
    position: absolute;
    border-radius: 16px;
    overflow: hidden;
  }

  /* Front */
  .card-front {
    left: 274px; top: 185px; width: 623px; height: 377px;
    background: linear-gradient(115deg, var(--navy-deep) 0%, var(--steel) 45%, var(--navy) 100%);
    color: var(--white);
  }
  .card-front .texture {
    position: absolute; inset: 0;
    background: linear-gradient(180deg, rgba(255,255,255,0.06), rgba(0,0,0,0.12));
  }
  .brand {
    position: absolute; display: flex; align-items: center; gap: 16px;
    font-weight: 700; letter-spacing: 2px; white-space: nowrap;
  }
  .brand-mark { display: block; border-radius: 3px; }
  .card-front .brand {
    left: 0; right: 0; top: 72px; justify-content: center;
    font-size: 50px; line-height: 60px; color: var(--white);
  }
  .card-front .brand-mark { width: 56px; height: 56px; border: 7px solid var(--white); }

  .intro-pill {
    position: absolute; left: 138px; top: 186px; width: 346px; height: 40px;
    border-radius: 20px; background: var(--navy-deep);
    border: 1px solid rgba(255,255,255,0.12);
    display: flex; align-items: center; justify-content: center;
    font-size: 16px; z-index: 2;
  }
  .products-band {
    position: absolute; left: 0; right: 0; top: 214px; height: 78px;
    background: var(--navy-band);
    display: flex; flex-direction: column; justify-content: center; align-items: center;
    padding-top: 10px;
    font-size: 16px; line-height: 22px;
  }
  .products-extra {
    position: absolute; left: 0; right: 0; top: 306px; text-align: center;
    font-size: 16px; line-height: 24px;
  }

  /* Back */
  .card-back {
    left: 276px; top: 608px; width: 618px; height: 374px;
    background: radial-gradient(ellipse at 45% 40%, var(--paper) 0%, var(--paper-shade) 100%);
    color: var(--ink);
  }
  .card-back .brand {
    left: 48px; top: 210px; font-size: 29px; line-height: 36px; color: var(--ink);
    flex-direction: column; gap: 20px;
  }
  .card-back .brand-mark { width: 70px; height: 70px; border: 9px solid var(--ink); }

  .contact { position: absolute; left: 343px; top: 80px; }
  .contact-name { font-size: 23px; font-weight: 700; line-height: 30px; }
  .contact-role { font-size: 16px; line-height: 22px; margin-top: 2px; }
  .contact-list { list-style: none; margin-top: 28px; }
  .contact-list li {
    display: flex; align-items: center; gap: 14px;
    font-size: 16px; line-height: 26px;
  }
  .contact-list svg { width: 16px; height: 16px; fill: var(--ink); }
  .contact-address { font-size: 16px; line-height: 25px; margin-top: 6px; }
</style>
</head>
<body>
<main class="canvas">

  <section class="card card-front">
    <div class="texture"></div>
    <div class="brand"><span class="brand-mark"></span>K T MASONRY</div>
    <div class="intro-pill">We are a building materials supplier of</div>
    <div class="products-band">
      <p>Ready Mixed Concrete, Bricks and Blocks, Quarry Products</p>
      <p>Quarry Products:- Gravel, Aggregates, Sand Etc.</p>
    </div>
    <div class="products-extra">
      <p>Cement Distributor/Retailer of Reputable Brands.</p>
      <p>Other Concrete Products Culverts, Wave Breakers, Concrete Retaining Blocks</p>
    </div>
  </section>

  <section class="card card-back">
    <div class="brand"><span class="brand-mark"></span>K T MASONRY</div>
    <div class="contact">
      <p class="contact-name">Daniel Harper</p>
      <p class="contact-role">Managing Director</p>
      <ul class="contact-list">
        <li>
          <svg viewBox="0 0 16 16" aria-hidden="true"><path d="M2 5c0-1.5 2.5-3 6-3s6 1.5 6 3v1.5h-3V5H5v1.5H2z M4 8h8l1.5 6h-11z"/></svg>
          000 0000 0000
        </li>
        <li>
          <svg viewBox="0 0 16 16" aria-hidden="true"><path d="M1 3h14v10H1z M2.5 4.5 8 9l5.5-4.5v-.2H2.5z" fill-rule="evenodd"/></svg>
          daniel@ktmasonry.com
        </li>
        <li>
          <svg viewBox="0 0 16 16" aria-hidden="true"><circle cx="8" cy="8" r="6.5" fill="none" stroke="#1b3a60" stroke-width="1.4"/><path d="M1.5 8h13M8 1.5c-3 3.5-3 9.5 0 13M8 1.5c3 3.5 3 9.5 0 13" fill="none" stroke="#1b3a60" stroke-width="1.2"/></svg>
          www.ktmasonry.com
        </li>
      </ul>
      <p class="contact-address">18 Harbour Rd., Point Cruz,<br>Honiara, SB 00100</p>
    </div>
  </section>

</main>
</body>
</html>
```